Web Site Design for a Finance (lending) Company

We are opening a new subsidiary that focuses on lending money in the real estate industry. We need a web site designed to represent the business.

The business is lending money to real estate investors. A typical client/borrower will be looking to borrow money to buy a house, renovate it and then sell it at a profit, all within 12 months or less.

Company name is RTV Finance. Our logo is attached.

Attached is a general outline for the web site. We're working on writing more text for each page but this should give you enough to get started with some ideas.

Competitor web site that I like a lot (as an example): https://dorvaleqcapital.example/. Many of the general items on this site match what we will need (description of loan programs, FAQ)

Target Market(s)

Real estate investors (generally individuals or small companies with just a few people) who are buying homes, renovating them and then selling them at a profit.

Industry/Entity Type

Finance

Coding

Coded - Design and coding required

Number of Pages Required

5+ page

Colors

Designer to choose colors to be used in the design.

Requirements
Must have
• Minimalist design. Clean lines without too much clutter. Some stock photography is ok but the photos should not be distracting. They should almost fade in to the background so that user can focus on the key information about what our company does instead. We are a finance company, not a design company, so the information about our products will be more interesting to site visitors than the art.
• Some minimalist examples from Snapboard:
• https://www.snapboardia.example/explore/minimalist-web-design/
Nice to have
• If you search in zoovle for "hard money lenders" you will find many examples of web sites from our competition. I have provided a link above to competitor web site that I like a lot.
• I have attached our logo in EPS format. Logo is green. Web site doesn't have to be green but it should be of a color that will work well with the logo.

```html
<!DOCTYPE html>
<html lang="en">
<head>
<meta charset="utf-8">
<title>RTV Finance</title>
<link href="https://fonts.googleapis.com/css2?family=Open+Sans:wght@400;600;700;800&display=swap" rel="stylesheet">
<style>
:root{
  --green:#1f5a3a;
  --green-dark:#134329;
  --green-soft:rgba(31,90,58,.88);
  --ink:#333;
  --muted:#666;
  --dark:#3a3a3a;
  --black:#1e1e1e;
  --line:#d5d5d5;
  --white:#fff;
}
*{box-sizing:border-box;margin:0;padding:0}
html,body{width:1200px;height:3240px;overflow:hidden}
body{font-family:"Open Sans",Arial,sans-serif;color:var(--ink);background:var(--white);position:relative}
a{color:inherit;text-decoration:none}

/* header + hero */
.hero{position:absolute;left:0;top:0;width:1200px;height:730px}
.hero-photo{position:absolute;inset:0;background:linear-gradient(180deg,#cfd9e2 0%,#b9c3c8 30%,#8d8f86 55%,#6a7a5a 80%,#4f6a3e 100%)}
.brand-panel{position:absolute;left:0;top:0;width:440px;height:200px}
.brand{position:absolute;left:40px;top:62px;display:flex;align-items:center;gap:18px;color:var(--white);font-weight:700;font-size:40px;line-height:1}
.brand-mark{width:34px;height:34px;background:var(--white)}
.topbar{position:absolute;left:440px;top:0;right:0;height:40px;background:var(--black);display:flex;justify-content:flex-end;align-items:center;gap:14px;padding-right:40px}
.topbar .dot{width:14px;height:14px;border-radius:50%;background:#bbb}
.nav{position:absolute;left:440px;top:40px;right:0;height:70px;background:var(--dark);display:flex;justify-content:flex-end;align-items:center;gap:48px;padding-right:44px;color:var(--white);font-size:17px;font-weight:600}
.callbar{position:absolute;left:800px;top:118px;right:40px;height:30px;background:var(--white);display:flex;justify-content:flex-end;align-items:center;padding-right:14px;font-size:15px;color:var(--ink)}
.hero-band{position:absolute;left:440px;right:0;top:600px;height:120px;background:var(--green-soft);color:var(--white);font-size:38px;line-height:1.25;padding:12px 0 0 40px}

/* shared */
.section-title{text-align:center;font-size:48px;font-weight:700;letter-spacing:.5px;color:var(--dark)}
.section-title span{color:var(--green)}
.lead{width:880px;margin:14px auto 0;text-align:center;font-size:15px;line-height:1.5;color:var(--muted)}
.read-more{display:inline-block;margin-top:8px;font-size:14px;font-weight:700;text-decoration:underline;color:var(--ink)}

/* about */
.about{position:absolute;top:750px;left:0;width:1200px}
.about-rule{width:1110px;height:1px;background:var(--line);margin:0 auto 16px}
.about-grid{display:flex;width:1110px;margin:40px auto 0;gap:60px}
.about-item{flex:1}
.about-head{display:flex;align-items:center;gap:16px;font-size:22px;font-weight:600;color:var(--dark)}
.about-icon{width:54px;height:54px;border-radius:50%;background:var(--green);flex:none}
.about-item p{margin-top:16px;font-size:14px;line-height:1.5;color:var(--muted)}

/* cta */
.cta{position:absolute;top:1080px;left:0;width:1200px;height:210px;background:var(--dark);color:var(--white);text-align:center;padding-top:38px}
.cta h2{font-size:32px;font-weight:700;line-height:1.3}
.cta-buttons{display:flex;justify-content:center;gap:20px;margin-top:22px}
.btn-outline{border:2px solid var(--white);padding:8px 30px;font-size:17px;font-weight:600;letter-spacing:.5px}

/* loans */
.loans{position:absolute;top:1330px;left:0;width:1200px}
.loan-grid{display:flex;width:1010px;margin:50px auto 0}
.loan{flex:1;padding:0 50px;text-align:center}
.loan + .loan{border-left:1px solid var(--line)}
.loan-name{display:flex;justify-content:center;align-items:center;gap:14px;height:150px;font-size:34px;font-weight:700;color:var(--dark)}
.loan-name i{width:26px;height:26px;background:var(--green)}
.loan p{font-size:14px;line-height:1.5;color:var(--muted);margin-top:16px}

/* team */
.team{position:absolute;top:1780px;left:0;width:1200px;height:440px;background:var(--green);padding-top:20px}
.team .section-title{color:var(--white)}
.team-grid{display:flex;gap:20px;width:1080px;margin:26px auto 0}
.member{flex:1;background:#e8e8e8}
.member-photo{height:205px;margin:8px 8px 0}
.member-info{text-align:center;padding:10px 6px 12px}
.member-info b{display:block;font-size:16px;color:var(--dark)}
.member-info span{display:block;font-size:12px;color:var(--muted);margin-top:2px;line-height:1.35}

/* news */
.news{position:absolute;top:2270px;left:0;width:1200px}
.news-grid{display:flex;gap:40px;width:1010px;margin:28px auto 0}
.news-item{flex:1;display:flex;gap:20px}
.news-thumb{width:240px;height:130px;flex:none}
.news-date{font-size:13px;color:var(--muted)}
.news-title{font-size:15px;font-weight:700;color:var(--green);line-height:1.3;margin-top:2px}
.news-text{font-size:14px;color:var(--muted);line-height:1.4;margin-top:12px}

/* testimonials */
.testimonials{position:absolute;top:2560px;left:0;width:1200px;height:280px;background:var(--dark);padding-top:22px;color:var(--white)}
.testimonials .section-title{color:var(--white)}
.quote-box{position:relative;width:830px;height:90px;margin:22px auto 0;background:var(--black);font-size:14px;line-height:1.5;text-align:center;padding:12px 60px;color:#ddd}
.quote-box cite{position:absolute;right:60px;bottom:8px;font-style:italic;font-size:13px}
.arrow{position:absolute;top:50%;transform:translateY(-50%);width:30px;height:40px;background:#888;display:flex;align-items:center;justify-content:center}
.arrow.prev{left:-34px}.arrow.next{right:-34px}
.dots{display:flex;justify-content:center;gap:14px;margin-top:26px}
.dots i{width:12px;height:12px;border-radius:50%;background:#888}
.dots i:first-child{background:var(--white)}

/* contact */
.contact{position:absolute;top:2870px;left:0;width:1200px}
.contact-grid{display:flex;gap:60px;width:800px;margin:30px auto 0}
.contact-form{width:430px;position:relative}
.field{height:34px;border:1px solid var(--line);margin-bottom:14px;font-size:13px;color:#999;padding:7px 12px}
.field.msg{height:100px;width:320px}
.send{position:absolute;right:0;bottom:14px;width:94px;height:100px;background:var(--green);color:var(--white);font-weight:700;font-size:15px;display:flex;flex-direction:column;align-items:center;justify-content:center;gap:8px}
.contact-info{flex:1;font-size:14px;color:var(--muted)}
.contact-info li{list-style:none;display:flex;gap:14px;align-items:flex-start;margin-bottom:20px;line-height:1.4}
.contact-info svg{flex:none}

.footer{position:absolute;left:0;bottom:0;width:1200px;height:50px;background:var(--green-dark);color:#d8e4dc;font-size:13px;display:flex;align-items:center;justify-content:center}
</style>
</head>
<body>

<header class="hero">
  <div class="hero-photo" role="img" aria-label="Photo of a modern apartment building with lawn and trees"></div>
  <svg class="brand-panel" viewBox="0 0 440 200" aria-hidden="true"><polygon points="0,0 440,0 440,110 360,200 0,200" fill="#1f5a3a"/></svg>
  <a class="brand" href="#"><span class="brand-mark"></span>RTV Finance</a>
  <div class="topbar"><i class="dot"></i><i class="dot"></i><i class="dot"></i></div>
  <nav class="nav"><a href="#">HOME</a><a href="#">ABOUT US</a><a href="#">LOANS</a><a href="#">RESOURCES</a><a href="#">CONTACT US</a></nav>
  <div class="callbar">Call Now : 123 456 7890</div>
  <div class="hero-band">Local real estate experts lending<br>to local real estate investors</div>
</header>

<section class="about">
  <h2 class="section-title">ABOUT <span>US</span></h2>
  <p class="lead">Lorem Ipsum is simply dummy text of the printing and typesetting industry. Lorem Ipsum has been the industry's standard dummy text ever since the 1500s, when an unknown printer took a galley of type and scrambled it to make a type specimen book.</p>
  <div class="about-grid">
    <div class="about-item">
      <div class="about-head"><span class="about-icon"></span>Mission</div>
      <p>Lorem Ipsum is simply dummy text of the printing and typesetting industry.</p>
      <a class="read-more" href="#">READ MORE</a>
    </div>
    <div class="about-item">
      <div class="about-head"><span class="about-icon"></span>Focus</div>
      <p>Lorem Ipsum is simply dummy text of the printing and typesetting industry.</p>
      <a class="read-more" href="#">READ MORE</a>
    </div>
    <div class="about-item">
      <div class="about-head"><span class="about-icon"></span>What makes us different</div>
      <p>Lorem Ipsum is simply dummy text of the printing and typesetting industry.</p>
      <a class="read-more" href="#">READ MORE</a>
    </div>
  </div>
</section>

<section class="cta">
  <h2>Lorem Ipsum is simply dummy text of the printing and<br>typesetting industry.</h2>
  <div class="cta-buttons"><a class="btn-outline" href="#">CHAT WITH US</a><a class="btn-outline" href="#">APPLY NOW</a></div>
</section>

<section class="loans">
  <h2 class="section-title"><span>LOANS</span> WE PROVIDE</h2>
  <p class="lead">Lorem Ipsum is simply dummy text of the printing and typesetting industry. Lorem Ipsum has been the industry's standard dummy text ever since the 1500s, when an unknown printer took a galley of type and scrambled it to make a type specimen book.</p>
  <div class="loan-grid">
    <div class="loan">
      <div class="loan-name"><i></i>RENOVEST</div>
      <p>Lorem Ipsum is simply dummy text of the printing and typesetting industry. Lorem Ipsum has been the industry's standard dummy text ever since the 1500s, when an unknown printer took a galley.</p>
      <a class="read-more" href="#">READ MORE</a>
    </div>
    <div class="loan">
      <div class="loan-name"><i></i>COMMERCIAL</div>
      <p>Lorem Ipsum is simply dummy text of the printing and typesetting industry. Lorem Ipsum has been the industry's standard dummy text ever since the 1500s, when an unknown printer took a galley.</p>
      <a class="read-more" href="#">READ MORE</a>
    </div>
  </div>
</section>

<section class="team">
  <h2 class="section-title">OUR TEAM</h2>
  <div class="team-grid">
    <div class="member">
      <div class="member-photo" role="img" aria-label="Portrait photo of a team member" style="background:linear-gradient(180deg,#dfe3e6,#4a5564)"></div>
      <div class="member-info"><b>Dorian K. Vale, Esq.</b><span>Partner &amp; Director of<br>Financial Lending</span></div>
    </div>
    <div class="member">
      <div class="member-photo" role="img" aria-label="Portrait photo of a team member" style="background:linear-gradient(180deg,#dcdcdc,#3b3b3b)"></div>
      <div class="member-info"><b>Mira T. Lowell</b><span>Managing Partner</span></div>
    </div>
    <div class="member">
      <div class="member-photo" role="img" aria-label="Portrait photo of a team member" style="background:linear-gradient(180deg,#e4e4e4,#2f3640)"></div>
      <div class="member-info"><b>Pell R. Hastings, Esq.</b><span>Senior Partner / Director of<br>Commercial Lending</span></div>
    </div>
    <div class="member">
      <div class="member-photo" role="img" aria-label="Portrait photo of a team member" style="background:linear-gradient(180deg,#e6e6e6,#5a4638)"></div>
      <div class="member-info"><b>Sorena Quill</b><span>Administrative Assistant</span></div>
    </div>
  </div>
</section>

<section class="news">
  <h2 class="section-title">LATEST <span>NEWS</span></h2>
  <div class="news-grid">
    <article class="news-item">
      <div class="news-thumb" role="img" aria-label="Photo of a laptop on a desk" style="background:linear-gradient(135deg,#6f93b5,#2f4f6e)"></div>
      <div>
        <div class="news-date">March 29, 2017</div>
        <div class="news-title">Lorem Ipsum is simply dummy text</div>
        <p class="news-text">Lorem Ipsum is simply dummy text of the printing and typesetting industry.</p>
      </div>
    </article>
    <article class="news-item">
      <div class="news-thumb" role="img" aria-label="Illustration of a house on a blue digital background" style="background:linear-gradient(135deg,#1d4d7a,#0a1f38)"></div>
      <div>
        <div class="news-date">March 29, 2017</div>
        <div class="news-title">Lorem Ipsum is simply dummy text</div>
        <p class="news-text">Lorem Ipsum is simply dummy text of the printing and typesetting industry.</p>
      </div>
    </article>
  </div>
</section>

<section class="testimonials">
  <h2 class="section-title">TESTIMONIALS</h2>
  <blockquote class="quote-box">
    <span class="arrow prev"><svg width="10" height="14" viewBox="0 0 10 14"><path d="M8 1 2 7l6 6" stroke="#fff" stroke-width="2" fill="none"/></svg></span>
    It is a long established fact that a reader will be distracted by the readable content of a page when looking at its layout. The point of using Lorem Ipsum is that it has a more-or-less normal distribution of letters.
    <cite>~ Linette Marsh</cite>
    <span class="arrow next"><svg width="10" height="14" viewBox="0 0 10 14"><path d="m2 1 6 6-6 6" stroke="#fff" stroke-width="2" fill="none"/></svg></span>
  </blockquote>
  <div class="dots"><i></i><i></i><i></i></div>
</section>

<section class="contact">
  <h2 class="section-title">CONTACT <span>US</span></h2>
  <div class="contact-grid">
    <form class="contact-form">
      <div class="field">Name</div>
      <div class="field">Email Id</div>
      <div class="field msg">How You Heard about us</div>
      <div class="send"><svg width="26" height="22" viewBox="0 0 26 22"><path d="M1 11 25 1l-6 20-6-7-6 3z" fill="#fff"/></svg>SEND</div>
    </form>
    <ul class="contact-info">
      <li><svg width="18" height="24" viewBox="0 0 18 24"><path d="M9 1a8 8 0 0 0-8 8c0 6 8 14 8 14s8-8 8-14a8 8 0 0 0-8-8z" fill="#666"/><circle cx="9" cy="9" r="3" fill="#fff"/></svg>Lorem Ipsum is simply dummy text of the printing and typesetting.</li>
      <li><svg width="18" height="18" viewBox="0 0 18 18"><path d="M4 1 1 4c0 7 6 13 13 13l3-3-4-3-2 2c-3-1-5-3-6-6l2-2z" fill="#666"/></svg>123 456 7890</li>
      <li><svg width="20" height="14" viewBox="0 0 20 14"><rect x="1" y="1" width="18" height="12" fill="none" stroke="#666" stroke-width="2"/><path d="m1 1 9 7 9-7" fill="none" stroke="#666" stroke-width="2"/></svg>info@rtvfinance.example</li>
    </ul>
  </div>
</section>

<footer class="footer">© RTV Finance. 2017. All Rights Reserved.</footer>

</body>
</html>
```